BOLD & MINIMALIST DESIGN NEEDED

We want a very bold but minimalistic business card design that is impactful and utilizes both sides of the business card. Our current logo is included for your use.

We want bold fonts and good use of negative space. We don't want the logo to overpower the design.

Target Market(s)

Professionals who are building new commercial buildings.

Industry/Entity Type

Construction

Contact Information for Business Card

Name, Title, email, office phone, cell phone, website

Font styles to use
Serif
Sans Serif

Requirements
Must have
• Bold design!

```html
<!DOCTYPE html>
<html lang="en">
<head>
<meta charset="utf-8">
<title>Ridgeline Design + Build — Business Card</title>
<link rel="stylesheet" href="https://fonts.googleapis.com/css2?family=Montserrat:wght@500;700;800&display=swap">
<style>
  :root {
    --backdrop: #a2fb35;
    --frame: #ffffff;
    --card: #ffffff;
    --forest: #2e5a2b;
    --lime: #8fe42e;
    --ink: #1b1b1b;
  }
  * { box-sizing: border-box; margin: 0; padding: 0; }
  html, body { width: 1200px; height: 773px; overflow: hidden; background: var(--frame); }
  .stage {
    position: absolute; left: 37px; top: 37px; width: 1126px; height: 694px;
    background: var(--backdrop);
  }
  .card {
    position: absolute; top: 225px; width: 469px; height: 269px;
    background: var(--card); overflow: hidden;
    box-shadow: 6px 8px 14px rgba(0,0,0,.28);
    font-family: "Montserrat", sans-serif; color: var(--ink);
  }
  .card--front { left: 60px; }
  .card--back { left: 559px; }
  .card__art { position: absolute; }
  .card--front .card__art {
    left: 0; right: 0; top: 150px; bottom: 0;
    background: linear-gradient(100deg, var(--lime) 0%, var(--lime) 30%, var(--forest) 70%, var(--forest) 100%);
  }
  .card--back .card__art {
    left: 330px; right: 0; top: 0; bottom: 0;
    background: linear-gradient(180deg, var(--forest) 0%, var(--forest) 55%, var(--lime) 100%);
  }
  .brand {
    position: absolute; display: flex; align-items: center; gap: 8px;
    font-weight: 800; color: var(--ink); text-transform: uppercase;
    line-height: 1.1; white-space: nowrap;
  }
  .brand__dot { background: var(--forest); flex: none; }
  .card--front .brand { left: 290px; top: 60px; font-size: 15px; letter-spacing: .5px; }
  .card--front .brand__dot { width: 14px; height: 14px; }
  .card--back .brand { left: 228px; top: 42px; font-size: 10px; }
  .card--back .brand__dot { width: 9px; height: 9px; }
  .person { position: absolute; left: 45px; top: 42px; }
  .person__name { font-size: 22px; font-weight: 500; line-height: 1; }
  .person__title { font-size: 10px; font-weight: 700; margin-top: 3px; }
  .contacts { position: absolute; left: 38px; top: 118px; list-style: none; }
  .contacts li { display: flex; align-items: center; gap: 9px; height: 32px; font-size: 11.5px; font-weight: 700; }
  .contacts svg { width: 22px; height: 22px; flex: none; }
</style>
</head>
<body>
<div class="stage">
  <section class="card card--front" aria-label="Card front">
    <div class="card__art" role="img" aria-label="Angular green band artwork"></div>
    <div class="brand"><span class="brand__dot"></span><span>Ridgeline<br>Design + Build</span></div>
  </section>

  <section class="card card--back" aria-label="Card back">
    <div class="card__art" role="img" aria-label="Angular green band artwork"></div>
    <div class="person">
      <p class="person__name">Your Name</p>
      <p class="person__title">Designation</p>
    </div>
    <div class="brand"><span class="brand__dot"></span><span>Ridgeline</span></div>
    <ul class="contacts">
      <li><svg viewBox="0 0 22 22" aria-hidden="true"><circle cx="11" cy="11" r="11" fill="var(--forest)"/><rect x="6" y="7.5" width="10" height="7" fill="none" stroke="#fff" stroke-width="1.3"/><path d="M6 7.5l5 4 5-4" fill="none" stroke="#fff" stroke-width="1.3"/></svg>yourmail@example.com</li>
      <li><svg viewBox="0 0 22 22" aria-hidden="true"><circle cx="11" cy="11" r="11" fill="var(--forest)"/><rect x="8" y="5.5" width="6" height="11" rx="1" fill="none" stroke="#fff" stroke-width="1.3"/><circle cx="11" cy="14.5" r=".8" fill="#fff"/></svg>+000 0000 00000</li>
      <li><svg viewBox="0 0 22 22" aria-hidden="true"><circle cx="11" cy="11" r="11" fill="var(--forest)"/><path d="M7.5 6.5l2 0 1 2.5-1.3 1a6 6 0 0 0 2.8 2.8l1-1.3 2.5 1v2a1 1 0 0 1-1 1A8 8 0 0 1 6.5 7.5a1 1 0 0 1 1-1z" fill="#fff"/></svg>+999 9999 99999</li>
      <li><svg viewBox="0 0 22 22" aria-hidden="true"><circle cx="11" cy="11" r="11" fill="var(--forest)"/><circle cx="11" cy="11" r="5.5" fill="none" stroke="#fff" stroke-width="1.2"/><ellipse cx="11" cy="11" rx="2.3" ry="5.5" fill="none" stroke="#fff" stroke-width="1.1"/><path d="M5.5 11h11" stroke="#fff" stroke-width="1.1"/></svg>www.companyname.com</li>
    </ul>
  </section>
</div>
</body>
</html>
```